Business Card For Halvenmoor Financial Consulting

Hi, I would like a business card designed. Bold, modern.
Please use the same design as the logo. I have also attached the website design to see the overall theme.
Wordmark Font
Color: Hex: #01AEF7

```html
<!DOCTYPE html>
<html lang="en">
<head>
<meta charset="utf-8">
<title>Halvenmoor Financial Consulting – Business Card</title>
<link href="https://fonts.googleapis.com/css2?family=Poppins:ital,wght@0,400;0,600;0,700;1,400;1,600&display=swap" rel="stylesheet">
<style>
  :root {
    --backdrop: #0d1217;
    --card: #16212c;
    --card-deep: #111a23;
    --accent: #01aef7;
    --accent-soft: #3f8fc4;
    --ink: #ffffff;
    --emboss: #1d3346;
  }
  * { box-sizing: border-box; margin: 0; padding: 0; }
  html, body {
    width: 1200px; height: 900px; overflow: hidden;
    background: var(--backdrop);
    font-family: "Poppins", sans-serif;
  }
  .sheet {
    position: relative; width: 1200px; height: 900px;
    display: flex; flex-direction: column; align-items: center; justify-content: center; gap: 40px;
  }
  .card {
    position: relative; width: 630px; height: 360px;
    background: var(--card);
    box-shadow: 0 18px 40px rgba(0,0,0,.55);
    overflow: hidden;
  }
  /* front */
  .brand {
    position: absolute; left: 40px; top: 40px;
    display: flex; align-items: center; gap: 12px;
  }
  .brand-square {
    flex: none;
    width: 26px; height: 26px; border: 3px solid var(--accent);
  }
  .brand-name {
    white-space: nowrap;
    color: var(--ink); font-weight: 700; font-size: 19px; letter-spacing: 1.5px;
    text-transform: uppercase;
  }
  .address {
    position: absolute; left: 40px; top: 128px;
    color: var(--ink); font-style: italic; font-size: 14px; line-height: 1.45;
  }
  .contacts {
    position: absolute; left: 40px; top: 190px; list-style: none;
    color: var(--ink); font-style: italic; font-size: 14px; line-height: 1.6;
  }
  .contacts li { display: flex; align-items: center; gap: 9px; }
  .contacts svg { width: 13px; height: 13px; fill: var(--accent); flex: none; }
  .person {
    position: absolute; right: 36px; top: 118px; text-align: right;
    padding-right: 18px; border-right: 6px solid var(--accent);
  }
  .person-name {
    color: var(--accent); font-weight: 700; font-style: italic; font-size: 20px;
    text-transform: uppercase; letter-spacing: .5px;
  }
  .person-role { color: var(--ink); font-style: italic; font-size: 15px; }
  .corner-panel {
    position: absolute; right: 0; bottom: 0; width: 250px; height: 130px;
    background: linear-gradient(160deg, var(--card-deep) 0%, #1a2b3b 60%, #355a78 100%);
    box-shadow: inset 6px 6px 12px rgba(0,0,0,.5);
  }
  /* back */
  .card-back { display: flex; align-items: center; justify-content: center; padding: 0 40px; }
  .back-brand { display: flex; align-items: center; gap: 16px; }
  .back-brand .brand-square { width: 40px; height: 40px; border: 4px solid var(--emboss); }
  .back-brand .brand-name { color: var(--accent-soft); font-size: 22px; letter-spacing: 1.5px; }
</style>
</head>
<body>
<main class="sheet">
  <section class="card card-front">
    <div class="brand">
      <span class="brand-square"></span>
      <span class="brand-name">Halvenmoor Financial Consulting</span>
    </div>
    <p class="address">1180 Larkfield Harbor Dr<br>Seaview CA 90417</p>
    <ul class="contacts">
      <li><svg viewBox="0 0 24 24"><path d="M6.6 10.8a15 15 0 0 0 6.6 6.6l2.2-2.2c.3-.3.7-.4 1-.2 1.1.4 2.3.6 3.6.6.6 0 1 .4 1 1V20c0 .6-.4 1-1 1A17 17 0 0 1 3 4c0-.6.4-1 1-1h3.5c.6 0 1 .4 1 1 0 1.3.2 2.5.6 3.6.1.3 0 .7-.2 1z"/></svg>555-014-2876</li>
      <li><svg viewBox="0 0 24 24"><path d="M2 5h20v14H2zm2 2v.5l8 5 8-5V7l-8 5z"/></svg>info@HalvenmoorConsulting.com</li>
      <li><svg viewBox="0 0 24 24"><path d="M12 2a10 10 0 1 0 0 20 10 10 0 0 0 0-20zm0 2c.9 0 2.2 1.9 2.7 5H9.3C9.8 5.9 11.1 4 12 4zm-7.7 7h3v2h-3a8 8 0 0 1 0-2zm12.4 0h3a8 8 0 0 1 0 2h-3zm-7.4 0h5.4v2H9.3zm0 4h5.4c-.5 3.1-1.8 5-2.7 5s-2.2-1.9-2.7-5z"/></svg>www.HalvenmoorConsulting.com</li>
    </ul>
    <div class="person">
      <p class="person-name">Marlo Renquist</p>
      <p class="person-role">President</p>
    </div>
    <div class="corner-panel" role="img" aria-label="Recessed corner panel with the brand emblem"></div>
  </section>

  <section class="card card-back">
    <div class="back-brand">
      <span class="brand-square"></span>
      <span class="brand-name">Halvenmoor Financial Consulting</span>
    </div>
  </section>
</main>
</body>
</html>
```